Webdesign für Steuerberaterin
Zielgruppe
Ich bin Steuerberaterin. Meine Zielgruppe sind sowohl Privatpersonen als auch Unternehmer sowie Männer und Frauen.
Aufgabenstellung
Bitte mein Logo und Foto mit berücksichtigen. Ich möchte keine Website, auf der alle 'Reiter' als eine Seite von oben nach unten durchlaufen. Sondern wirklich einzelne, voneinander getrennte Seiten.

```html
<!DOCTYPE html>
<html lang="de">
<head>
<meta charset="utf-8">
<title>Maren Brodtke – Steuerberaterin</title>
<link rel="stylesheet" href="https://fonts.googleapis.com/css2?family=PT+Sans:wght@400;700&family=Tinos&display=swap">
<style>
  :root {
    --sidebar: #1c1a1f;
    --gold: #c0902a;
    --gold-dark: #a87a22;
    --gold-band: #d8b53c;
    --text: #555459;
    --text-strong: #4a494e;
    --page: #ffffff;
  }
  * { margin: 0; padding: 0; box-sizing: border-box; }
  html, body { width: 1200px; height: 960px; overflow: hidden; background: var(--page); }
  body { position: relative; font-family: "PT Sans", sans-serif; color: var(--text); }

  .sidebar { position: absolute; left: 0; top: 0; width: 243px; height: 933px; background: var(--sidebar); }
  .nav { position: absolute; left: 60px; list-style: none; font-size: 14px; color: var(--gold); }
  .nav li { position: absolute; left: 0; white-space: nowrap; }

  .brand { position: absolute; left: 507px; top: 70px; width: 400px; text-align: center; }
  .brand-mark { display: inline-block; width: 14px; height: 14px; border-radius: 50%; background: var(--gold); margin-bottom: 10px; }
  .brand-name { font-family: "Tinos", serif; font-size: 30px; color: var(--gold); line-height: 1; }
  .brand-role { margin-top: 8px; font-family: "Tinos", serif; font-size: 8px; letter-spacing: 2px; color: var(--text-strong); }

  .divider { position: absolute; left: 419px; top: 181px; width: 596px; height: 2px; background: var(--gold); }

  .portrait { position: absolute; left: 161px; top: 221px; width: 401px; height: 289px;
    background: radial-gradient(ellipse at 50% 40%, #f7f6f4 0%, #e3e0dc 55%, #c9c4be 100%); }
  .portrait::after { content: ""; position: absolute; left: 110px; bottom: 0; width: 190px; height: 150px;
    background: #1b1d2a; border-radius: 90px 90px 0 0; }

  .welcome { position: absolute; left: 598px; top: 256px; width: 560px; }
  .welcome h1 { font-family: "Tinos", serif; font-weight: 400; font-size: 24px; color: var(--gold-dark); line-height: 1; margin-left: 2px; }
  .welcome .lead { margin-top: 43px; font-weight: 700; font-size: 16.5px; color: var(--text-strong); }
  .welcome p.body { font-size: 15.5px; line-height: 22.7px; }
  .p1 { margin-top: 26px; }
  .p2 { margin-top: 24px; }
  .p3 { margin-top: 24px; }

  .footer-band { position: absolute; left: 0; top: 933px; width: 1200px; height: 27px;
    background: linear-gradient(180deg, #dcbb42 0%, #cfa935 100%); }
</style>
</head>
<body>
  <aside class="sidebar">
    <ul class="nav">
      <li style="top:256px">Über mich</li>
      <li style="top:298px; left:1px">Leistungen</li>
      <li style="top:342px">Kontakt</li>
      <li style="top:477px">Impressum</li>
      <li style="top:520px">Datenschutz</li>
    </ul>
  </aside>

  <header class="brand">
    <span class="brand-mark"></span>
    <div class="brand-name">Maren Brodtke</div>
    <div class="brand-role">STEUERBERATERIN</div>
  </header>

  <div class="divider"></div>

  <div class="portrait" role="img" aria-label="Porträtfoto der Steuerberaterin im dunklen Blazer vor heller Steinwand"></div>

  <main class="welcome">
    <h1>Schön, dass Sie da sind</h1>
    <p class="lead">Ich freue mich, dass Sie den Weg zu mir gefunden haben!</p>
    <p class="body p1">Sie sind bei mir genau richtig:<br>
      Egal, ob Sie Privatperson sind, die Ihre Einkommensteuer-Erklärung<br>
      in vertrauensvolle Hände geben möchte,<br>
      oder Unternehmer, der sich z.B. das „Rundum-Sorglos-Paket“<br>
      mit Buchführung, Jahresabschluss und Steuererklärungen wünscht.</p>
    <p class="body p2">Schauen Sie sich hier gerne um und melden Sie sich bei mir<br>
      – ich bin bei jedem steuerlichen Thema<br>
      gerne Ihr kompetenter und zuverlässiger Ansprechpartner.</p>
    <p class="body p3">Für mich ist es eine Selbstverständlichkeit,<br>
      dass ich auch nach mehr als 12 Jahren Berufserfahrung<br>
      durch permanente Fortbildungen immer auf dem aktuellsten Stand<br>
      der relevanten Gesetze und Verordnungen bin.<br>
      Nur so kann ich Sie bestmöglich beraten.</p>
  </main>

  <div class="footer-band"></div>
</body>
</html>
```